Business card for law firm

Need business card for new law firm. Think confident, authoritative, conservative, but not stuffy or old-fashioned.

Contact Information for Business Card

Content for card - logo (uploaded), plus the following:

Paul Whitcombe (larger font)
Managing Partner (larger font, but not as large as name)
Level 9, 7 Ferris Lane
Sydney NSW 2000
Main Tel 02 9364 2710
Direct Tel 02 8472 3159
Email paul@qvlegal.com.au
www.qvlegal.com.au

Letterhead design should include logo plus:
Level 9, 7 Ferris Lane
Sydney NSW 2000
Tel 02 8472 3159
www.qvlegal.com.au

```html
<!DOCTYPE html>
<html lang="en">
<head>
<meta charset="UTF-8">
<title>Quayvale Lawyers – Business Card</title>
<link href="https://fonts.googleapis.com/css2?family=Roboto:wght@400;700&display=swap" rel="stylesheet">
<style>
  :root {
    --page-bg: #d9dadc;
    --navy: #0b1f5e;
    --navy-deep: #081849;
    --white: #ffffff;
    --ink: #111111;
    --rule: #1a1a1a;
  }
  * { box-sizing: border-box; margin: 0; padding: 0; }
  html, body { width: 1200px; height: 1000px; overflow: hidden; }
  body {
    background: var(--page-bg);
    font-family: "Roboto", Arial, sans-serif;
    display: flex;
    flex-direction: column;
    align-items: center;
    justify-content: center;
    gap: 56px;
  }
  .card {
    position: relative;
    width: 640px;
    height: 390px;
    border-radius: 26px;
    overflow: hidden;
    box-shadow: 0 10px 28px rgba(0,0,0,.18);
  }

  /* Back */
  .card-back { background: var(--navy); }
  .card-back .swoosh { position: absolute; inset: 0; }
  .brand {
    display: flex;
    flex-direction: column;
    align-items: center;
  }
  .brand-square { width: 58px; height: 58px; margin-bottom: 16px; }
  .brand-name {
    font-weight: 400;
    font-size: 34px;
    letter-spacing: 5px;
    text-transform: uppercase;
    white-space: nowrap;
  }
  .card-back .brand {
    position: absolute;
    right: 48px;
    top: 100px;
    width: 330px;
  }
  .card-back .brand-square { background: var(--white); }
  .card-back .brand-name { color: var(--white); }
  .card-back .back-web {
    margin-top: 40px;
    color: var(--white);
    font-size: 15px;
    letter-spacing: 1px;
  }

  /* Front */
  .card-front { background: var(--white); }
  .card-front .brand {
    position: absolute;
    left: 0; right: 0;
    top: 40px;
  }
  .card-front .brand-square { background: var(--navy); }
  .card-front .brand-name { color: var(--ink); }
  .holder {
    position: absolute;
    left: 0; right: 0;
    top: 198px;
    text-align: center;
    white-space: nowrap;
  }
  .holder-name {
    color: var(--navy);
    font-weight: 700;
    font-size: 23px;
    text-transform: uppercase;
  }
  .holder-role {
    color: var(--ink);
    font-size: 16px;
    margin-left: 6px;
  }
  .rule {
    position: absolute;
    left: 0; right: 0;
    top: 238px;
    height: 2px;
    background: var(--rule);
  }
  .band {
    position: absolute;
    left: 0; right: 0;
    top: 246px;
    bottom: 0;
    background: var(--navy);
    color: var(--white);
    display: flex;
    justify-content: center;
    align-items: center;
    gap: 28px;
    font-size: 15px;
    line-height: 1.5;
  }
  .address { text-align: right; }
  .divider { width: 2px; height: 92px; background: var(--white); }
  .contacts { list-style: none; }
  .contacts li { display: flex; align-items: center; gap: 7px; }
  .contacts svg { width: 13px; height: 13px; flex: none; }
</style>
</head>
<body>

  <section class="card card-back">
    <svg class="swoosh" viewBox="0 0 640 390" preserveAspectRatio="none" aria-hidden="true">
      <path d="M0 0 H300 C250 40 250 110 300 160 C220 150 120 190 60 260 C110 300 110 350 70 390 H0 Z" fill="var(--navy-deep)"/>
    </svg>
    <div class="brand">
      <div class="brand-square"></div>
      <div class="brand-name">Quayvale Lawyers</div>
      <div class="back-web">www.qvlegal.com.au</div>
    </div>
  </section>

  <section class="card card-front">
    <div class="brand">
      <div class="brand-square"></div>
      <div class="brand-name">Quayvale Lawyers</div>
    </div>
    <div class="holder">
      <span class="holder-name">Paul Whitcombe</span><span class="holder-role">Managing Partner</span>
    </div>
    <div class="rule"></div>
    <div class="band">
      <address class="address" style="font-style:normal">
        Level 9, 7 Ferris Lane<br>Sydney NSW 2000
      </address>
      <div class="divider"></div>
      <ul class="contacts">
        <li>Main Tel 02 9364 2710</li>
        <li>Direct Tel 02 8472 3159</li>
        <li>
          <svg viewBox="0 0 14 14" aria-hidden="true"><rect x="1" y="3" width="12" height="8" fill="none" stroke="#fff" stroke-width="1.3"/><path d="M1 3 L7 8 L13 3" fill="none" stroke="#fff" stroke-width="1.3"/></svg>
          paul@qvlegal.com.au
        </li>
        <li>
          <svg viewBox="0 0 14 14" aria-hidden="true"><circle cx="7" cy="7" r="5.8" fill="none" stroke="#fff" stroke-width="1.2"/><ellipse cx="7" cy="7" rx="2.5" ry="5.8" fill="none" stroke="#fff" stroke-width="1"/><path d="M1.2 7 H12.8" stroke="#fff" stroke-width="1"/></svg>
          www.qvlegal.com.au
        </li>
      </ul>
    </div>
  </section>

</body>
</html>
```